Design for a group involved in running bars and restaurants. They are all based in Singapore

I run a few concept bars & restaurants
1) Traditional French restaurant called Le Morvandel
2) french steakhouse chain called Les Tonnelles
3) Wine & Whisky bar called Flagon and Cask

Know more at
www.lestonnelles.sg
www.lemorvandel.sg
www.flagonandcask.com

Idea is to get people to feel that these are all part of one group although they have different brandings and logo.

Mention List of outlets (preferably on the reverse):
1) Le Morvandel
42 Verlane Street, Singapore 071286, Tel: +65.6310.4582
2) Les Tonnelles Merrow Hill
9 Merrow Hill Road, Singapore 072315, Tel: +65.6518.2946
3) Les Tonnelles Quai Vert
37 Tolbrook Quay, #02-05 Singapore, Tel: +65.6841.7390
4) Flagon and Cask
16 Merrow Hill Road, Singapore 072341, Tel: +65.6518.6172

Target Market(s)

People who generally love food, wine and whiskies based in Singapore

Industry/Entity Type

Restaurant

Contact Information for Business Card

Prefer to keep all logos

Font styles to use
Script

Requirements
Must have
• Need to keep all logos.
• Mention List of outlets:
• 1) Le Morvandel
• 42 Verlane Street, Singapore 071286, Tel: +65.6310.4582
• 2) Les Tonnelles Merrow Hill
• 9 Merrow Hill Road, Singapore 072315, Tel: +65.6518.2946
• 3) Les Tonnelles Quai Vert
• 37 Tolbrook Quay, #02-05 Singapore, Tel: +65.6841.7390
• 4) Flagon and Cask
• 16 Merrow Hill Road, Singapore 072341, Tel: +65.6518.6172
Nice to have
• Devesh Malor
• +65.9387.5146
• devesh.malor@morvandelgroup.example
Should not have
• No designation required

```html
<!DOCTYPE html>
<html lang="en">
<head>
<meta charset="utf-8">
<title>Devesh Malor – Business Card</title>
<link href="https://fonts.googleapis.com/css2?family=Roboto:wght@400;700&family=Roboto+Condensed:wght@300;400;700&display=swap" rel="stylesheet">
<style>
  :root {
    --backdrop: #e9e6e1;
    --card: #ffffff;
    --ink: #111111;
    --text: #444444;
    --text-soft: #555555;
    --rule: #b9b9b9;
    --green: #1f7a43;
    --gold: #cfae5a;
    --black: #1a1a1a;
  }
  * { margin: 0; padding: 0; box-sizing: border-box; }
  html, body {
    width: 1125px;
    height: 1200px;
    overflow: hidden;
    background: var(--backdrop);
  }
  .canvas { position: relative; width: 1125px; height: 1200px; }

  .card {
    position: absolute;
    left: 145px;
    width: 800px;
    height: 456px;
    background: var(--card);
    box-shadow: 0 2px 6px rgba(0,0,0,0.18);
  }
  .card--front { top: 96px; }
  .card--back { top: 611px; }

  /* Front */
  .holder-name {
    position: absolute;
    right: 467px;
    top: 210px;
    font-family: "Roboto", sans-serif;
    font-weight: 700;
    font-size: 29px;
    letter-spacing: 0.3px;
    color: var(--ink);
  }
  .front-divider {
    position: absolute;
    left: 357px;
    top: 196px;
    width: 1px;
    height: 64px;
    background: var(--rule);
  }
  .contact-list {
    position: absolute;
    left: 385px;
    top: 203px;
    list-style: none;
    font-family: "Roboto Condensed", sans-serif;
    font-weight: 400;
    font-size: 19px;
    color: var(--text-soft);
  }
  .contact-list li {
    display: flex;
    align-items: center;
    height: 24px;
  }
  .contact-list svg { width: 16px; margin-right: 9px; flex: none; }

  /* Back */
  .outlet {
    position: absolute;
    font-family: "Roboto Condensed", sans-serif;
    font-size: 19px;
    line-height: 24px;
    color: var(--text);
  }
  .outlet__name { font-weight: 700; }
  .outlet__line { font-weight: 300; }
  .outlet__tel { font-weight: 400; color: #333; }

  .outlet--morvandel { left: 184px; top: 72px; }
  .outlet--quai { left: 544px; top: 68px; }
  .outlet--merrow { left: 183px; top: 290px; }
  .outlet--flagon { left: 589px; top: 295px; }

  .brand-mark {
    position: absolute;
    display: flex;
    flex-direction: column;
    align-items: center;
    justify-content: center;
    gap: 8px;
    font-family: "Roboto Condensed", sans-serif;
    font-weight: 700;
    font-size: 15px;
    text-align: center;
    line-height: 17px;
  }
  .brand-mark__dot {
    width: 40px;
    height: 40px;
    border-radius: 50%;
    border: 2px solid currentColor;
  }
  .brand-mark--morvandel { left: 58px; top: 68px; width: 110px; height: 102px; color: var(--green); }
  .brand-mark--quai { left: 428px; top: 44px; width: 100px; height: 118px; color: var(--black); }
  .brand-mark--merrow { left: 58px; top: 295px; width: 110px; height: 100px; color: var(--black); }
  .brand-mark--flagon { left: 435px; top: 285px; width: 128px; height: 110px; color: var(--gold); }

  .web-band {
    position: absolute;
    left: 73px;
    top: 206px;
    width: 657px;
    height: 40px;
    border-top: 2px solid var(--rule);
    border-bottom: 2px solid var(--rule);
    display: flex;
    align-items: center;
    justify-content: center;
    font-family: "Roboto", sans-serif;
    font-size: 19px;
    color: var(--text-soft);
  }
  .web-band .sep { margin: 0 14px; color: var(--text-soft); }
  .web--morvandel { color: var(--green); }
  .web--flagon { color: var(--gold); }
</style>
</head>
<body>
<div class="canvas">

  <section class="card card--front" aria-label="Business card front">
    <h1 class="holder-name">DEVESH MALOR</h1>
    <div class="front-divider"></div>
    <ul class="contact-list">
      <li>
        <svg viewBox="0 0 16 20" height="20" aria-hidden="true"><rect x="2.5" y="1" width="11" height="18" rx="1.5" fill="none" stroke="#222" stroke-width="2"/><rect x="6" y="15.5" width="4" height="1.5" fill="#222"/></svg>
        +65.9387.5146
      </li>
      <li>
        <svg viewBox="0 0 16 12" height="12" aria-hidden="true"><rect x="0.5" y="1" width="15" height="10" fill="#222"/><path d="M0.5 1 L8 7 L15.5 1" fill="none" stroke="#fff" stroke-width="1.3"/></svg>
        devesh.malor@morvandelgroup.example
      </li>
    </ul>
  </section>

  <section class="card card--back" aria-label="Business card back">
    <div class="brand-mark brand-mark--morvandel"><span class="brand-mark__dot"></span>Le Morvandel</div>
    <div class="outlet outlet--morvandel">
      <div class="outlet__name">Le Morvandel</div>
      <div class="outlet__line">42 Verlane Street</div>
      <div class="outlet__line">Singapore 071286</div>
      <div class="outlet__tel">Tel: +65.6310.4582</div>
    </div>

    <div class="brand-mark brand-mark--quai"><span class="brand-mark__dot"></span>Les Tonnelles</div>
    <div class="outlet outlet--quai">
      <div class="outlet__name">Les Tonnelles Quai Vert</div>
      <div class="outlet__line">37 Tolbrook Quay</div>
      <div class="outlet__line">#02-05 Singapore</div>
      <div class="outlet__tel">Tel: +65.6841.7390</div>
    </div>

    <div class="web-band">
      <span class="web--morvandel">www.lemorvandel.sg</span>
      <span class="sep">|</span>
      <span class="web--tonnelles">www.lestonnelles.sg</span>
      <span class="sep">|</span>
      <span class="web--flagon">www.flagonandcask.com</span>
    </div>

    <div class="brand-mark brand-mark--merrow"><span class="brand-mark__dot"></span>Les Tonnelles</div>
    <div class="outlet outlet--merrow">
      <div class="outlet__name">Les Tonnelles Merrow Hill</div>
      <div class="outlet__line">9 Merrow Hill Road</div>
      <div class="outlet__line">Singapore 072315</div>
      <div class="outlet__tel">Tel: +65.6518.2946</div>
    </div>

    <div class="brand-mark brand-mark--flagon"><span class="brand-mark__dot"></span>Flagon and Cask</div>
    <div class="outlet outlet--flagon">
      <div class="outlet__name">Flagon and Cask</div>
      <div class="outlet__line">16 Merrow Hill Road</div>
      <div class="outlet__line">Singapore 072341</div>
      <div class="outlet__tel">Tel: +65.6518.6172</div>
    </div>
  </section>

</div>
</body>
</html>
```